Tech business card design

We need an amazing business card design for our new business 'Pexla' a marketing tech startup based in Sydney, Australia. We provide an online marketplace for businesses to search and buy advertising media, connect with service providers and learn more about marketing. We wish to communicate 'cool tech', reliability and professionalism and design based around our logo.

Target Market(s)

Business Owners

Contact Information for Business Card

Name
Position
Email Address
Website
Phone Number

Font styles to use
Other font styles liked:
• Avenir & Avenir Next

Colors

Designer to choose colors to be used in the design.

```html
<!DOCTYPE html>
<html lang="en">
<head>
<meta charset="UTF-8">
<title>Pexla Business Card</title>
<link rel="stylesheet" href="https://fonts.googleapis.com/css2?family=Nunito+Sans:wght@400;600;800&display=swap">
<style>
  :root {
    --stage: #1d1d1f;
    --navy: #1c2050;
    --charcoal: #262427;
    --white: #ffffff;
    --stripe-grey: #8d8d94;
    --stripe-blue: #3a4186;
    --text-light: #f2f3f8;
    --mark-faint: #5c6194;
  }
  * { margin: 0; padding: 0; box-sizing: border-box; }
  html, body {
    width: 1200px; height: 900px; overflow: hidden;
    background: var(--stage);
    font-family: "Nunito Sans", Arial, sans-serif;
  }
  .canvas { position: relative; width: 1200px; height: 900px; }
  .card {
    position: absolute; width: 640px; height: 370px;
    border-radius: 24px; overflow: hidden;
    box-shadow: 0 18px 40px rgba(0,0,0,0.55);
  }
  .card--front { left: 110px; top: 60px; }
  .card--back { left: 450px; top: 470px; background: var(--navy); }
  .card__art { position: absolute; inset: 0; width: 100%; height: 100%; }
  .brand {
    position: absolute; left: 44px; top: 92px;
    font-weight: 800; font-size: 92px; line-height: 1;
    color: var(--navy); letter-spacing: -2px;
  }
  .brand__tm { position: absolute; left: 318px; top: 150px; font-size: 11px; font-weight: 800; color: var(--navy); }
  .holder { position: absolute; right: 40px; top: 30px; text-align: right; color: var(--text-light); }
  .holder__name { font-weight: 800; font-size: 19px; letter-spacing: 0.5px; }
  .holder__role { font-weight: 600; font-size: 13px; margin-top: 1px; }
  .contact {
    position: absolute; right: 36px; top: 196px; list-style: none;
    color: var(--text-light); font-size: 15px; text-align: right;
  }
  .contact li { display: flex; justify-content: flex-end; align-items: center; gap: 8px; height: 25px; }
  .contact svg { width: 13px; height: 13px; fill: var(--text-light); }
  .address {
    position: absolute; left: 40px; bottom: 30px;
    color: var(--text-light); font-size: 16px; line-height: 1.3;
  }
  .back-mark {
    position: absolute; left: 0; right: 0; top: 100px; text-align: center;
    font-weight: 800; font-size: 150px; line-height: 1;
    color: var(--mark-faint); letter-spacing: -3px;
  }
  .back-mark__tm { position: absolute; right: 68px; top: 120px; font-size: 14px; font-weight: 800; color: var(--mark-faint); }
</style>
</head>
<body>
<main class="canvas">
  <section class="card card--front" aria-label="Business card front">
    <svg class="card__art" viewBox="0 0 640 370" preserveAspectRatio="none" aria-hidden="true">
      <rect width="640" height="370" fill="var(--navy)"/>
      <path d="M0 0 H640 V118 C540,116 470,180 370,232 C260,288 120,300 0,292 Z" fill="var(--charcoal)"/>
      <path d="M0 292 C120,300 260,288 370,232 C470,180 540,116 640,118" fill="none" stroke="var(--stripe-grey)" stroke-width="5"/>
      <path d="M0 300 C120,308 262,296 374,240 C474,188 542,126 640,128" fill="none" stroke="var(--stripe-blue)" stroke-width="2"/>
      <path d="M0 0 H356 C396,90 382,200 300,246 C220,288 100,284 0,270 Z" fill="var(--white)"/>
      <path d="M356 0 C396,90 382,200 300,246 C220,288 100,284 0,270" fill="none" stroke="var(--stripe-grey)" stroke-width="4"/>
      <path d="M364 0 C404,92 390,206 304,254 C222,296 100,292 0,278" fill="none" stroke="var(--stripe-blue)" stroke-width="2"/>
    </svg>
    <div class="brand">Pexla</div>
    <div class="brand__tm">TM</div>
    <div class="holder">
      <p class="holder__name">JOHN SMITH</p>
      <p class="holder__role">Position</p>
    </div>
    <ul class="contact">
      <li>012-345-6789
        <svg viewBox="0 0 24 24"><path d="M6.6 10.8a15 15 0 0 0 6.6 6.6l2.2-2.2a1 1 0 0 1 1-.25 11.4 11.4 0 0 0 3.6.57 1 1 0 0 1 1 1V20a1 1 0 0 1-1 1A17 17 0 0 1 3 4a1 1 0 0 1 1-1h3.5a1 1 0 0 1 1 1c0 1.25.2 2.45.57 3.6a1 1 0 0 1-.25 1z"/></svg>
      </li>
      <li>info@pexla.com
        <svg viewBox="0 0 24 24"><path d="M2 5h20v14H2z M4 7v.4l8 5 8-5V7z" fill-rule="evenodd"/></svg>
      </li>
      <li>www.pexla.com
        <svg viewBox="0 0 24 24"><circle cx="12" cy="12" r="10" fill="none" stroke="currentColor" stroke-width="2" style="stroke:var(--text-light)"/><path d="M2 12h20M12 2c3 3 3 17 0 20M12 2c-3 3-3 17 0 20" fill="none" style="stroke:var(--text-light)" stroke-width="1.6"/></svg>
      </li>
    </ul>
    <p class="address">Street Name, City Name<br>Zipcode:012345</p>
  </section>

  <section class="card card--back" aria-label="Business card back">
    <div class="back-mark">Pexla</div>
    <div class="back-mark__tm">TM</div>
  </section>
</main>
</body>
</html>
```